Sophisticated, clean website reflecting my feminine, playful side to sell my abstract art,

I need a website no more than 3 pages to showcase my paintings, a little about me and some contact info. I do abstracts so looking for something a little edgy, yet feminine and current.
Updates

Hi there, These are some artists websites that I Iike: Marnelvoss.com (I like how airy it is) peterwallombry.com garethpolvens.com (I like how it scrolls) I'll need a place for a photo ( a headshot-i do not have it yet so I'll need to be able to upload that later) as well as an area for my bio. Also, it's important that I will be able to upload any new photos and descriptions easily so it should be user friendly. Lastly, I like in a sunny place so would like to have this seem upbeat and playful as that is how i like to paint. thanks-I'm trying to upload my photos now -

Target Market(s)

ppl ages 35-70 who want large scale art for their homes

Industry/Entity Type

art

Coding

Coded - Design and coding required

Number of Pages Required

3 page

Colors

Designer to choose colors to be used in the design.

Requirements
Must have
• photos of my art, a place for my bio, be easy to reach me. tasteful-nothing too "in your face" -my clients are pretty high end and organized. They like clean lines
Nice to have
• sophisticated background, muted tones in the back-similar clean font throughout-no cursive
Should not have
• too many dark areas. Too many blocks of color. Too serious.

```html
<!DOCTYPE html>
<html lang="en">
<head>
<meta charset="utf-8">
<title>Helena Sorrell — Art Gallery</title>
<link href="https://fonts.googleapis.com/css2?family=Playfair+Display:wght@400;500&family=Source+Sans+3:wght@400;600;700&display=swap" rel="stylesheet">
<style>
:root{
  --ink:#161616;
  --white:#ffffff;
  --soft:#f1f1f1;
  --olive:#9b9c84;
  --gold:#f2cf12;
  --muted:#c9c9c9;
  --footer:#2a2a2a;
  --line:#d8d8d8;
}
*{box-sizing:border-box;margin:0;padding:0}
html,body{width:1200px;height:5068px;overflow:hidden;background:var(--white)}
body{position:relative;font-family:"Source Sans 3",Arial,sans-serif;color:var(--ink)}
.abs{position:absolute}
.serif{font-family:"Playfair Display",Georgia,serif;font-weight:400}
.art{position:absolute}
.round-icon{position:absolute;width:30px;height:30px;border:1.5px solid var(--ink);border-radius:50%;display:flex;align-items:center;justify-content:center}
.round-icon svg{width:14px;height:14px}
.btn-dark{position:absolute;background:#000;color:#fff;font-weight:700;font-size:13px;display:flex;align-items:center;justify-content:center}
.section-title{position:absolute;left:0;width:1200px;text-align:center;font-size:33px}
/* header */
.brand{left:0;width:1200px;top:20px;text-align:center;font-size:29px;font-weight:500}
.login{left:1015px;top:18px;width:84px;height:47px;border:1px solid #999;font-weight:700;font-size:13px;display:flex;align-items:center;justify-content:center}
.nav{left:0;width:1200px;top:84px;display:flex;justify-content:center;gap:24px;font-size:10px;font-weight:600}
.nav .active{text-decoration:underline}
/* hero */
.hero{left:0;top:130px;width:1200px;height:500px;background:linear-gradient(100deg,#6b4a31 0 6%,#d9d6c9 6% 10%,#3f8f4a 18%,#7ab85a 38%,#2f7a52 52%,#c9cf8a 66%,#3f9a56 80%,#e8e6d8 100%)}
.hero-title{left:0;width:1200px;top:272px;text-align:center;color:#fff;font-size:48px;font-weight:500}
.explore{left:507px;top:370px;width:186px;height:47px;background:#fff;color:#000}
.dots{left:575px;top:593px;display:flex;gap:6px}
.dots span{width:11px;height:11px;border-radius:50%;background:#bbb}
.dots span.on{background:#000}
/* cards */
.card-img{top:832px;width:310px;height:270px}
.stars{position:absolute;color:var(--gold);font-size:17px;letter-spacing:1px}
.stars .off{color:var(--muted)}
.price{position:absolute;width:310px;text-align:center;top:1152px;color:var(--olive);font-size:21px;font-weight:600}
.card-name{position:absolute;width:310px;text-align:center;top:1192px;font-size:21px;font-weight:600}
.buy{position:absolute;top:1240px;width:174px;height:50px;background:var(--olive);color:#fff;font-size:12px;font-weight:700;display:flex;align-items:center;justify-content:center}
.sq{position:absolute;top:1240px;width:50px;height:50px;border:1.5px solid var(--olive);display:flex;align-items:center;justify-content:center}
.sq svg{width:24px;height:24px}
/* about */
.about-panel{left:594px;top:1384px;width:606px;height:604px;background:var(--soft)}
.about-title{left:662px;top:1472px;font-size:34px}
.about-text{left:662px;top:1578px;width:436px;font-size:13.2px;line-height:22.5px;color:#333}
/* reviews */
.review{position:absolute;top:2208px;width:468px;height:205px;border:1.5px solid #555;border-right:5px solid #111;border-bottom:5px solid #111;background:#fff;padding:24px 24px;font-size:13.5px;line-height:22.5px}
.tail{position:absolute}
.avatar{position:absolute;width:62px;height:62px;border-radius:50%;background:linear-gradient(160deg,#8c8c8c,#5f5f5f)}
.rev-name{position:absolute;font-size:12px;font-weight:700}
.rev-sub{position:absolute;font-size:13.5px}
.arrow{position:absolute;width:26px;height:26px;border-radius:50%;display:flex;align-items:center;justify-content:center}
/* gallery */
.gallery-bg{left:0;top:2634px;width:1200px;height:1392px;background:#f2f2f2}
.name-mark{left:446px;top:3192px;width:307px;height:273px;display:flex;align-items:center;justify-content:center;font-size:40px;font-weight:700;color:#1f1a17;text-align:center;line-height:1.1}
/* footer */
.footer{left:0;top:4643px;width:1200px;height:425px;background:var(--footer);color:#fff}
.foot-mark{left:100px;top:4725px;width:172px;height:220px;display:flex;align-items:center;font-size:40px;font-weight:700;color:#fff;line-height:1.1}
.foot-h{font-size:22px;color:#fff}
.foot-link{position:absolute;font-size:13px;color:#fff}
.contact-icon{position:absolute;width:28px;height:28px;border:1.5px solid #fff;border-radius:50%;display:flex;align-items:center;justify-content:center}
.contact-icon svg{width:13px;height:13px}
.email-box{left:820px;top:4800px;width:197px;height:62px;background:#fff;color:#777;font-size:11px;padding:0 24px;display:flex;align-items:center}
.send{left:1017px;top:4800px;width:82px;height:62px;background:var(--olive);display:flex;align-items:center;justify-content:center}
.foot-social{position:absolute;top:4898px;width:28px;height:28px;border:1.5px solid #fff;border-radius:50%}
.legal{position:absolute;top:5032px;font-size:9.5px;color:#ddd}
</style>
</head>
<body>

<!-- header -->
<header>
  <div class="round-icon" style="left:101px;top:26px" aria-label="Social profile"></div>
  <div class="round-icon" style="left:145px;top:26px" aria-label="Social profile"></div>
  <div class="round-icon" style="left:189px;top:26px" aria-label="Social profile"></div>
  <div class="round-icon" style="left:233px;top:26px" aria-label="Email"><svg viewBox="0 0 16 16" fill="none" stroke="#111" stroke-width="1.6"><rect x="1.5" y="3.5" width="13" height="9" rx="1"/><path d="M2 4l6 5 6-5"/></svg></div>
  <div class="round-icon" style="left:277px;top:26px" aria-label="Phone"><svg viewBox="0 0 16 16" fill="none" stroke="#111" stroke-width="1.6"><path d="M3 2h3l1.5 3.5-2 1.2a8 8 0 004 4l1.2-2L14 10v3a1 1 0 01-1 1A11 11 0 012 3a1 1 0 011-1z"/></svg></div>

  <div class="abs brand serif">Helena Sorrell</div>

  <div class="round-icon" style="left:823px;top:26px"><svg viewBox="0 0 16 16" fill="#111"><circle cx="8" cy="5" r="3"/><path d="M2 15a6 6 0 0112 0z"/></svg></div>
  <div class="round-icon" style="left:869px;top:26px"><svg viewBox="0 0 16 16" fill="none" stroke="#111" stroke-width="1.6"><path d="M8 14S2 10 2 5.5A3 3 0 018 4a3 3 0 016 1.5C14 10 8 14 8 14z"/></svg></div>
  <div class="round-icon" style="left:913px;top:26px"><svg viewBox="0 0 16 16" fill="none" stroke="#111" stroke-width="1.5"><path d="M1 2h2.5l2 8h7.5l1.5-6H4.5"/><circle cx="6.5" cy="13" r="1"/><circle cx="12" cy="13" r="1"/></svg></div>
  <div class="abs login">Login</div>

  <nav class="abs nav">
    <span class="active">Home</span><span>Featured Collection</span><span>Reviews</span><span>Art Gallery</span><span>About The Artist</span>
  </nav>
</header>

<!-- hero -->
<section>
  <div class="abs hero" role="img" aria-label="Close-up of a green and teal abstract painting on a wooden easel"></div>
  <h1 class="abs hero-title serif">Welcome To My Art Gallery</h1>
  <div class="btn-dark explore">Explore All</div>
  <div class="abs dots"><span></span><span class="on"></span><span></span></div>
</section>

<!-- featured collection -->
<section>
  <h2 class="section-title serif" style="top:726px">Featured Collection</h2>

  <div class="art card-img" style="left:100px;background:linear-gradient(135deg,#c96a22,#2f7a6e 40%,#e9e4dc 60%,#1d1d1d 85%,#b98a3a)" role="img" aria-label="Abstract painting with orange, teal and white bursts"></div>
  <div class="art card-img" style="left:446px;background:linear-gradient(90deg,#2e8a84 0 8%,#d8d2c2 8% 55%,#1f3e8a 65%,#1a3374)" role="img" aria-label="Abstract painting with grey canvas and deep blue drips"></div>
  <div class="art card-img" style="left:791px;background:linear-gradient(180deg,transparent 0 88%,#c9955a 88%),linear-gradient(90deg,#8a9ab8 0 28%,#0f8a7a 32% 64%,#e3ddd0 68% 80%,#8a9ab8 84%)" role="img" aria-label="Abstract painting with a teal band between pale blue panels"></div>

  <div class="stars" style="left:209px;top:1118px">★★★★<span class="off">★</span></div>
  <div class="stars" style="left:555px;top:1118px">★★★★<span class="off">★</span></div>
  <div class="stars" style="left:900px;top:1118px">★★★★★</div>

  <div class="price" style="left:100px">$50.00</div>
  <div class="price" style="left:446px">$68.00</div>
  <div class="price" style="left:791px">$75.90</div>

  <div class="card-name" style="left:100px">Coloured Painting</div>
  <div class="card-name" style="left:446px">Coloured Painting</div>
  <div class="card-name" style="left:791px">Coloured Painting</div>

  <div class="buy" style="left:104px">Buy Now</div>
  <div class="sq" style="left:290px"><svg viewBox="0 0 24 24" fill="none" stroke="#666" stroke-width="1.5"><path d="M12 20S3 14 3 8a4.5 4.5 0 019-1 4.5 4.5 0 019 1c0 6-9 12-9 12z"/></svg></div>
  <div class="sq" style="left:353px"><svg viewBox="0 0 24 24" fill="none" stroke="#666" stroke-width="1.5"><path d="M2 3h3l3 12h11l2-9H7"/><circle cx="9" cy="19" r="1.5"/><circle cx="17" cy="19" r="1.5"/></svg></div>

  <div class="buy" style="left:449px">Buy Now</div>
  <div class="sq" style="left:636px"><svg viewBox="0 0 24 24" fill="none" stroke="#666" stroke-width="1.5"><path d="M12 20S3 14 3 8a4.5 4.5 0 019-1 4.5 4.5 0 019 1c0 6-9 12-9 12z"/></svg></div>
  <div class="sq" style="left:699px"><svg viewBox="0 0 24 24" fill="none" stroke="#666" stroke-width="1.5"><path d="M2 3h3l3 12h11l2-9H7"/><circle cx="9" cy="19" r="1.5"/><circle cx="17" cy="19" r="1.5"/></svg></div>

  <div class="buy" style="left:795px">Buy Now</div>
  <div class="sq" style="left:981px"><svg viewBox="0 0 24 24" fill="none" stroke="#666" stroke-width="1.5"><path d="M12 20S3 14 3 8a4.5 4.5 0 019-1 4.5 4.5 0 019 1c0 6-9 12-9 12z"/></svg></div>
  <div class="sq" style="left:1044px"><svg viewBox="0 0 24 24" fill="none" stroke="#666" stroke-width="1.5"><path d="M2 3h3l3 12h11l2-9H7"/><circle cx="9" cy="19" r="1.5"/><circle cx="17" cy="19" r="1.5"/></svg></div>
</section>

<!-- about -->
<section>
  <div class="art" style="left:0;top:1384px;width:594px;height:604px;background:linear-gradient(120deg,#3b3a2c,#6d6445 40%,#8f7c58 60%,#2c2a22)" role="img" aria-label="Portrait photo of the artist"></div>
  <div class="abs about-panel"></div>
  <h2 class="abs about-title serif">About The Artist</h2>
  <p class="abs about-text">Lorem ipsum dolor sit amet, consectetur adipiscing elit. Consequat quis turpis adipiscing tincidunt. Fames ut lectus tempus quis lacus nunc arcu. Mi, ultrices varius ultrices massa aliquam odio enim quam. Quisque libero sed eget pellentesque imperdiet. At et lorem habitant amet morbi velit, sed eu lorem. Egestas egestas mattis ultrices aliquam. Malesuada at malesuada convallis feugiat. Pharetra venenatis odio duis quis semper amet. Amet justo, enim ac lacus, aenean elementum. Commodo fermentum viverra consectetur at elit mauris a orci. Quis molestie cursus nisi lorem mi.<br>Suscipit cursus sagittis odio ut sit in aliquam at amet. Leo orci sed mauris sit morbi mi diam vestibulum. Ultrices aliquam donec semper gravida nibh dictum dui. Suspendisse ultrices egestas dui a, faucibus. Eget a id placerat semper consectetur. Integer augue tortor etiam quis. Euismod imperdiet elit proin fames felis lectus justo.</p>
</section>

<!-- reviews -->
<section>
  <h2 class="section-title serif" style="top:2102px">Reviews</h2>
  <div class="arrow" style="left:40px;top:2307px;background:#111"><svg width="12" height="12" viewBox="0 0 12 12" fill="#fff"><path d="M8 2L3 6l5 4z"/></svg></div>
  <div class="arrow" style="left:1134px;top:2307px;background:#999"><svg width="12" height="12" viewBox="0 0 12 12" fill="#fff"><path d="M4 2l5 4-5 4z"/></svg></div>

  <div class="review" style="left:102px">Lorem ipsum dolor sit amet, consectetur adipiscing elit. Habitasse pulvinar malesuada turpis ullamcorper. Etiam arcu elit euismod quisque. Pulvinar turpis pellentesque duis leo lectus turpis eu. Egestas netus fermentum vitae fusce porta. Vitae quam aliquam molestie commodo amet euismod. Cras in hendrerit congue viverra bibendum.</div>
  <svg class="tail" style="left:172px;top:2408px" width="56" height="48" viewBox="0 0 56 48"><path d="M2 0v44L46 0" fill="#fff" stroke="#111" stroke-width="4"/></svg>
  <div class="avatar" style="left:159px;top:2478px" role="img" aria-label="Reviewer portrait"></div>
  <div class="rev-name" style="left:242px;top:2488px">OWEN LARCH</div>
  <div class="rev-sub" style="left:242px;top:2512px">Lorem ipsum dolor</div>
  <div class="stars" style="left:415px;top:2496px">★★★★★</div>

  <div class="review" style="left:618px;top:2214px">Lorem ipsum dolor sit amet, consectetur adipiscing elit. Habitasse pulvinar malesuada turpis ullamcorper. Etiam arcu elit euismod quisque. Pulvinar turpis pellentesque duis leo lectus turpis eu. Egestas netus fermentum vitae fusce porta. Vitae quam aliquam molestie commodo amet euismod. Cras in hendrerit congue viverra bibendum.</div>
  <svg class="tail" style="left:688px;top:2414px" width="56" height="48" viewBox="0 0 56 48"><path d="M2 0v44L46 0" fill="#fff" stroke="#111" stroke-width="4"/></svg>
  <div class="avatar" style="left:676px;top:2478px" role="img" aria-label="Reviewer portrait"></div>
  <div class="rev-name" style="left:759px;top:2488px">MILES ARDEN</div>
  <div class="rev-sub" style="left:759px;top:2512px">Lorem ipsum dolor</div>
  <div class="stars" style="left:932px;top:2496px">★★★★★</div>
</section>

<!-- art gallery -->
<section>
  <div class="abs gallery-bg"></div>
  <h2 class="section-title serif" style="top:2730px">Art Gallery</h2>
  <div class="art" style="left:102px;top:2836px;width:468px;height:312px;background:linear-gradient(90deg,#1d8a86 0 13%,#d9d3c4 13% 62%,#213f8c 72%,#1b3678)" role="img" aria-label="Grey and blue abstract painting"></div>
  <div class="art" style="left:630px;top:2836px;width:468px;height:312px;background:linear-gradient(135deg,#b34a1e,#e2c23a 35%,#efe8d8 55%,#d3a827 75%,#2b4f8a)" role="img" aria-label="Yellow and orange swirling abstract painting"></div>
  <div class="art" style="left:102px;top:3192px;width:344px;height:273px;background:linear-gradient(120deg,#2c5fa0,#e9e3d4 35%,#d8a93a 55%,#eae4d6 70%,#a97b52 90%)" role="img" aria-label="Abstract painting with blue and yellow circles"></div>
  <div class="abs name-mark">Helena<br>Sorrell</div>
  <div class="art" style="left:753px;top:3192px;width:345px;height:273px;background:linear-gradient(90deg,#9c7048 0 12%,#e6e4df 12% 88%,#9c7048 88%),#ddd" role="img" aria-label="Pale abstract painting with blue drips"></div>
  <div class="art" style="left:102px;top:3510px;width:468px;height:312px;background:linear-gradient(100deg,#8a6a48 0 7%,#4c9a4e 20%,#e6e4d8 40%,#2f8a52 60%,#b9c86e 80%,#3c8c4a)" role="img" aria-label="Green and teal abstract painting"></div>
  <div class="art" style="left:630px;top:3510px;width:468px;height:312px;background:linear-gradient(120deg,#9a7550 0 5%,#5a2a22 20%,#ebe3dc 45%,#7a3b2c 65%,#c9968a 85%)" role="img" aria-label="Burgundy and blush abstract painting"></div>
  <div class="btn-dark" style="left:507px;top:3885px;width:186px;height:50px">View All</div>
</section>

<!-- studio feed -->
<section>
  <h2 class="section-title serif" style="top:4124px">Follow My Studio Feed</h2>
  <div class="art" style="left:104px;top:4230px;width:239px;height:207px;background:linear-gradient(135deg,#e8e2ea,#6b4a9a 45%,#3a3470 65%,#d9cfe2)" role="img" aria-label="Purple abstract painting"></div>
  <div class="art" style="left:356px;top:4230px;width:238px;height:207px;background:linear-gradient(135deg,#efe2d8,#a8452a 40%,#7a2c1e 60%,#e5cbb8)" role="img" aria-label="Rust red swirling abstract painting"></div>
  <div class="art" style="left:607px;top:4230px;width:240px;height:207px;background:linear-gradient(135deg,#6a4a52,#d89aa0 40%,#efd4cf 60%,#4a2e32)" role="img" aria-label="Pink floral abstract painting"></div>
  <div class="art" style="left:859px;top:4230px;width:239px;height:207px;background:linear-gradient(135deg,#d59aa0,#5a3a3e 40%,#e8bdb8 60%,#8a5a5e)" role="img" aria-label="Rose toned abstract painting"></div>
  <div class="btn-dark" style="left:508px;top:4500px;width:186px;height:50px">Follow</div>
</section>

<!-- footer -->
<footer>
  <div class="abs footer"></div>
  <div class="abs foot-mark">Helena<br>Sorrell</div>

  <h3 class="abs foot-h serif" style="left:385px;top:4738px">Quick Links</h3>
  <span class="foot-link" style="left:385px;top:4797px">Home</span>
  <span class="foot-link" style="left:385px;top:4829px">Featured Collection</span>
  <span class="foot-link" style="left:385px;top:4860px">Reviews</span>
  <span class="foot-link" style="left:385px;top:4892px">Art Gallery</span>
  <span class="foot-link" style="left:385px;top:4923px">About The Artist</span>

  <h3 class="abs foot-h serif" style="left:557px;top:4738px">Contact Info</h3>
  <div class="contact-icon" style="left:559px;top:4801px"><svg viewBox="0 0 16 16" fill="none" stroke="#fff" stroke-width="1.6"><path d="M3 2h3l1.5 3.5-2 1.2a8 8 0 004 4l1.2-2L14 10v3a1 1 0 01-1 1A11 11 0 012 3a1 1 0 011-1z"/></svg></div>
  <span class="foot-link" style="left:607px;top:4806px">000.000.0000</span>
  <div class="contact-icon" style="left:559px;top:4846px"><svg viewBox="0 0 16 16" fill="#fff"><path d="M8 1a5 5 0 015 5c0 4-5 9-5 9S3 10 3 6a5 5 0 015-5z"/><circle cx="8" cy="6" r="2" fill="#2a2a2a"/></svg></div>
  <span class="foot-link" style="left:607px;top:4851px">gfgfsgfgddhgjhytrtshgjhfd</span>
  <div class="contact-icon" style="left:559px;top:4891px"><svg viewBox="0 0 16 16" fill="none" stroke="#fff" stroke-width="1.6"><rect x="1.5" y="3.5" width="13" height="9" rx="1"/><path d="M2 4l6 5 6-5"/></svg></div>
  <span class="foot-link" style="left:607px;top:4896px">studio@helenasorrell.art</span>

  <h3 class="abs foot-h serif" style="left:820px;top:4738px">Newsletter</h3>
  <div class="abs email-box">Email</div>
  <div class="abs send"><svg width="24" height="24" viewBox="0 0 24 24" fill="none" stroke="#fff" stroke-width="1.5"><path d="M22 2L2 10l8 3 3 8z"/><path d="M22 2L10 13"/></svg></div>
  <div class="foot-social" style="left:821px" aria-label="Social profile"></div>
  <div class="foot-social" style="left:866px" aria-label="Social profile"></div>
  <div class="foot-social" style="left:910px" aria-label="Social profile"></div>

  <span class="legal" style="left:104px">Terms Of Use</span>
  <span class="legal" style="left:197px">Privacy Policy</span>
  <span class="legal" style="left:904px">© 2022 Art Gallery. ALL RIGHTS RESERVED</span>
</footer>

</body>
</html>
```